Core Value Graphic for a Service Disabled and Minority Certified contractor

My company, Keystone Aid Partners, is a US Federal Contractor that hires veterans and service disabled veterans. Our website is www.keystoneaid7.example. We work hard to maintain a 50:50 split between veterans and non-veterans on our team. Our tagline is "To Find a Better Way." We are continually looking to integrate technology and efficiency into all that we do.

I want a way to express our company core values visually so that our employees and customers alike can read them and get a sense of who we are, what drives us to succeed, and what makes up our team DNA.

I need an artist like you to help me represent our core values visually. In a manner that I can print it out on an 8"X11" sheet of paper or a large 48" X 48" poster, without losing the visual clarity or that it pixelates out of focus. I am looking for a color scheme that is patriotic with Red, White, and Blues and similar hues. I would also like to incorporate my logo and tagline into the design in some manner.

I have attached several examples of a Core Value Grids from other companies. I am hopeful it will inspire you, and a get your brain juices flowing to provide me with a knockout Core Value Grid that will rock only you can provide! I also include a copy of my company Core Values and a copy of our Logo.

Looking forward to seeing your creations. Thanks.

Target Market(s)

Employees, any potential strategic alliance partners, and customers.

Industry/Entity Type

Contractor

Requirements
Must have
• Patriotic feel and have my logo someplace on the document.

```html
<!DOCTYPE html>
<html lang="en">
<head>
<meta charset="utf-8">
<title>Keystone Aid Partners – Our Core Values</title>
<link rel="stylesheet" href="https://fonts.googleapis.com/css2?family=Arimo:wght@700&family=Open+Sans:wght@700;800&display=swap">
<style>
  :root {
    --navy: #1c2149;
    --navy-deep: #141838;
    --red: #a3161c;
    --red-bright: #c0222a;
    --blue-grey: #7a7fa8;
    --white: #ffffff;
    --ink: #111111;
    --page: #eeeeee;
    --heading-font: "Arimo", Arial, sans-serif;
    --body-font: "Open Sans", Arial, sans-serif;
  }
  * { margin: 0; padding: 0; box-sizing: border-box; }
  html, body { width: 1200px; height: 1000px; overflow: hidden; }
  body { background: var(--page); position: relative; }

  .poster {
    position: absolute; left: 150px; top: 50px;
    width: 800px; height: 800px;
    transform: scale(1.125); transform-origin: 0 0;
    background: var(--white);
  }

  .header-band {
    position: absolute; left: 0; top: 0; width: 800px; height: 100px;
    background: linear-gradient(90deg, #fff 0%, #fff 22%, #c6c8da 34%, var(--blue-grey) 46%, #5a5d78 60%, #2a2a2e 78%, #1a1a1a 100%);
  }
  .brand {
    position: absolute; left: 28px; top: 30px;
    display: flex; align-items: center; gap: 9px;
  }
  .brand-square { width: 22px; height: 22px; background: var(--red); }
  .brand-name {
    font-family: var(--body-font); font-weight: 800; font-size: 17px;
    line-height: 1.05; color: var(--navy); text-transform: uppercase;
  }
  .title {
    position: absolute; font-family: var(--heading-font); font-weight: 700;
    color: var(--white); white-space: nowrap; letter-spacing: 0.5px;
  }
  .title .small { font-size: 42px; }
  .title .big { font-size: 56px; }
  .header-band .title { right: 26px; top: 14px; }

  .field {
    position: absolute; left: 0; top: 100px; width: 800px; height: 620px;
    background:
      radial-gradient(ellipse 320px 260px at 730px 200px, rgba(170,24,34,0.85), transparent 70%),
      radial-gradient(ellipse 280px 220px at 110px 420px, rgba(120,20,40,0.55), transparent 70%),
      radial-gradient(ellipse 260px 300px at 560px 560px, rgba(50,60,130,0.6), transparent 70%),
      linear-gradient(160deg, #2a2e62 0%, var(--navy) 45%, var(--navy-deep) 100%);
  }

  .footer-band {
    position: absolute; left: 0; top: 720px; width: 800px; height: 80px;
    background: linear-gradient(90deg, #1a1a1a 0%, #2a2a2e 24%, #5a5d78 44%, var(--blue-grey) 58%, #c6c8da 72%, #fff 86%);
  }
  .footer-band .title { left: 16px; top: 6px; }

  .connectors { position: absolute; left: 0; top: 0; width: 800px; height: 800px; }

  .value-tab {
    position: absolute; z-index: 2; height: 30px;
    background: linear-gradient(180deg, var(--red-bright), var(--red));
    color: var(--white); font-family: var(--heading-font); font-weight: 700;
    font-size: 12px; line-height: 13px; text-align: center;
    padding-top: 2px; white-space: nowrap;
  }
  .value-card {
    position: absolute; z-index: 1; background: var(--white);
    padding: 6px 8px; text-align: center;
    font-family: var(--body-font); font-weight: 700; font-size: 7.2px;
    line-height: 1.6; color: var(--ink); text-transform: uppercase;
  }
  .value-card h3 {
    font-size: 10.5px; line-height: 1.3; color: var(--red);
    font-weight: 700; margin-top: 2px;
  }
  .value-card p { margin-bottom: 1px; }

  .tagline-box {
    position: absolute; left: 343px; top: 370px; width: 108px; height: 85px;
    background: var(--navy-deep); border: 1.5px solid var(--white);
    color: var(--white); font-family: var(--heading-font); font-weight: 700;
    font-size: 19px; line-height: 23px; text-align: center; padding-top: 5px;
  }
</style>
</head>
<body>
<main class="poster">
  <header class="header-band">
    <div class="brand">
      <span class="brand-square"></span>
      <span class="brand-name">Keystone Aid<br>Partners</span>
    </div>
    <h1 class="title"><span class="small">OUR </span><span class="big">CORE VALUES</span></h1>
  </header>

  <div class="field" role="img" aria-label="Dark navy background with sweeping red and blue flag-like ribbons"></div>

  <svg class="connectors" viewBox="0 0 800 800" aria-hidden="true">
    <defs>
      <g id="star">
        <circle r="15" fill="var(--navy-deep)" stroke="#fff" stroke-width="1"/>
        <polygon points="0,-13 3.8,-4.2 13,-4 5.8,2 8,12 0,6.5 -8,12 -5.8,2 -13,-4 -3.8,-4.2" fill="#fff" stroke="var(--navy-deep)" stroke-width="1"/>
      </g>
    </defs>
    <g stroke="#fff" stroke-width="1" fill="none">
      <polyline points="367,370 367,217 345,217"/>
      <polyline points="425,370 425,305 455,305"/>
      <polyline points="451,398 505,398 505,420 538,420"/>
      <polyline points="343,425 289,425 262,425"/>
      <polyline points="430,455 430,472 481,472"/>
    </g>
    <use href="#star" x="367" y="217"/>
    <use href="#star" x="425" y="305"/>
    <use href="#star" x="505" y="398"/>
    <use href="#star" x="289" y="425"/>
    <use href="#star" x="481" y="468"/>
  </svg>

  <div class="tagline-box">TO FIND<br>A BETTER<br>WAY</div>

  <!-- Safety -->
  <div class="value-tab" style="left:95px;top:118px;width:138px;">Everyone comes back<br>to the Green Zone.</div>
  <section class="value-card" style="left:92px;top:148px;width:253px;height:210px;">
    <h3>WHAT IT MEANS</h3>
    <p>Safety takes precedence over every phase of the day’s operation.</p>
    <h3>HOW TO EXPRESS IT</h3>
    <p>Anyone can call a stop to the work in progress if an unsafe act is occurring. In fact, it is each team member’s duty to do so, rectify the unsafe issue, then proceed. Never hesitate; everyone comes back. Finally, each after action review begins with discussing safety issues. We always let everyone on the team know of an unsafe situation, so it can be avoided in the future.</p>
    <h3>RESULT</h3>
    <p>All team members go home to their loved ones each day to pursue their individual happiness</p>
  </section>

  <!-- Innovation -->
  <div class="value-tab" style="left:460px;top:119px;width:118px;">Boldly go.<br>Seek. Find.</div>
  <section class="value-card" style="left:455px;top:149px;width:250px;height:213px;">
    <h3>WHAT IT MEANS</h3>
    <p>We weave innovation into the fabric that makes up our company.</p>
    <h3>HOW TO EXPRESS IT</h3>
    <p>We’re early adopters of technology. We quickly evaluate new technologies or processes that could separate us from our competition. Then we implement and evaluate these new technologies. We dump it quickly if we see it is not helping us achieve “Commander’s Intent.” We have the guts to be first. We iterate continuously and attack, attack, attack.</p>
    <h3>RESULT</h3>
    <p>We will be ahead of our competition. It’s one mechanism that helps us scale. Prosperity favors the bold!</p>
  </section>

  <!-- Teamwork -->
  <div class="value-tab" style="left:33px;top:366px;width:132px;">Never leave your<br>wingman.</div>
  <section class="value-card" style="left:23px;top:396px;width:239px;height:241px;">
    <h3>WHAT IT MEANS</h3>
    <p>We always help your team members be successful. Commitment to each other and to our own personal integrity is the fuel that empowers us.</p>
    <h3>HOW TO EXPRESS IT</h3>
    <p>If a wingman is having challenges accomplishing their individual priorities or completing their assigned mission, volunteer to help them to do so.<br>This goes for subs/suppliers as well. We help those who help us succeed! Always look to establish the best win-win relationship possible, and do what you can to support them if they get into a bind.</p>
    <h3>RESULT</h3>
    <p>Be there for them and they will be there for us.</p>
  </section>

  <!-- Leadership -->
  <div class="value-tab" style="left:545px;top:366px;width:145px;">Troops (Team Members)<br>eat first.</div>
  <section class="value-card" style="left:538px;top:396px;width:242px;height:180px;">
    <h3>WHAT IT MEANS</h3>
    <p>No leader will put themselves ahead of their subordinates.</p>
    <h3>HOW TO EXPRESS IT</h3>
    <p>We lead by example. Demonstrate the moral courage and discipline to do the right thing at the highest level of quality.</p>
    <h3>RESULT</h3>
    <p>Every new team member will quickly realize their leaders genuinely care for their welfare and success. This is the best way to drive esprit de corps and achieve excellence.</p>
  </section>

  <!-- Learning -->
  <div class="value-tab" style="left:288px;top:468px;width:120px;">Fail quickly<br>and learn</div>
  <section class="value-card" style="left:280px;top:498px;width:245px;height:219px;">
    <h3>WHAT IT MEANS</h3>
    <p>If you’re not making mistakes, you’re not taking enough chances or getting out of your comfort zone.</p>
    <h3>HOW TO EXPRESS IT</h3>
    <p>Use your best judgment when trying something new. But, don’t let your pride keep you from saying, “I was wrong” when your idea doesn’t work. We trust you will know when it’s time to dump the idea, or stop doing something that doesn’t work.</p>
    <h3>RESULT</h3>
    <p>No one will ever be penalized for making a mistake. Don’t be afraid to try something you believe will work. That’s how we grow ourselves and our team members.</p>
  </section>

  <footer class="footer-band">
    <h2 class="title"><span class="small">OUR </span><span class="big">CORE VALUES</span></h2>
  </footer>
</main>
</body>
</html>
```